Automotive component supplier needs a business card design

We need a business card design for our company called Velran Global Components Ltd based in the UK. We are a supplier of interior and exterior components to premium car manufacturers such as Corvel Ashby, Hadley Fenn, Marquist and Tavarelli. We would like to see a modern business card design that uses the colour blue.

Target Market(s)

Premium automotive car manufacturers.

Industry/Entity Type

Automotive

Contact Information for Business Card

Company Name : Velran Global Components Limited
Address: 17 Marlow Yard, Upper Heath, Warwick, CV31 8QL, United Kingdom
Web Address : www.velrancomponents-example.co.uk

Font styles to use
Other font styles liked:
• Helvetica

Colors
3176b5
0255a3
85acd3
cfdeed
cee9f5
85cae6
34a6d7
0692cd
9bcb3c

Requirements
Must have
• Clear company logo and a mixture of blue colours.
Nice to have
• A high quality modern image.
Should not have
• Multiple colours.

```html
<!DOCTYPE html>
<html lang="en">
<head>
<meta charset="utf-8">
<title>Velran Global Components – Business Card</title>
<link rel="stylesheet" href="https://fonts.googleapis.com/css2?family=Open+Sans:wght@400;600&display=swap">
<style>
  :root {
    --backdrop: #2b2624;
    --card: #0b0b0b;
    --card-edge: #1a1a1a;
    --blue: #0692cd;
    --blue-light: #34a6d7;
    --green: #9bcb3c;
    --text: #f2f2f2;
    --divider: #2a2a2a;
  }
  * { margin: 0; padding: 0; box-sizing: border-box; }
  html, body {
    width: 1200px; height: 900px; overflow: hidden;
    background: var(--backdrop);
    font-family: "Open Sans", Arial, sans-serif;
  }
  .stage {
    position: relative; width: 1200px; height: 900px;
    display: flex; align-items: center; justify-content: center; gap: 48px;
  }
  .card {
    position: relative; width: 520px; height: 316px;
    background: var(--card);
    box-shadow: 0 0 0 1px var(--card-edge), 0 18px 40px rgba(0,0,0,.45);
  }
  /* Front: contact side */
  .card-front .brand-mark {
    position: absolute; left: 46px; top: 118px;
    display: flex; align-items: center; gap: 12px;
  }
  .brand-mark .brand-name {
    color: var(--blue); font-weight: 600; font-size: 44px; letter-spacing: 1px; line-height: 1;
  }
  .brand-mark .brand-dot {
    width: 22px; height: 22px; border-radius: 4px; background: var(--green);
  }
  .card-front .contact-panel {
    position: absolute; left: 290px; top: 42px; right: 20px; bottom: 40px;
    border-left: 1px solid var(--divider);
    padding-left: 18px; color: var(--text);
  }
  .person-name { color: var(--blue-light); font-weight: 600; font-size: 16px; line-height: 1.2; }
  .person-role { font-size: 12px; margin-top: 2px; }
  .address { font-size: 11.5px; line-height: 1.45; margin-top: 18px; }
  .contact-list { list-style: none; margin-top: 16px; font-size: 12px; }
  .contact-list li { display: flex; align-items: center; gap: 9px; line-height: 1.55; }
  .contact-list svg { width: 10px; height: 10px; fill: var(--blue-light); flex: none; }
  .web { font-size: 11px; }
  /* Back: brand side */
  .card-back { display: flex; align-items: center; justify-content: center; }
  .card-back .brand-lockup { display: flex; align-items: center; gap: 14px; }
  .card-back .brand-name {
    color: var(--blue); font-weight: 600; font-size: 30px; letter-spacing: .5px;
  }
  .card-back .brand-dot { width: 16px; height: 16px; border-radius: 3px; background: var(--green); }
</style>
</head>
<body>
<main class="stage">
  <section class="card card-front" aria-label="Business card, contact side">
    <div class="brand-mark">
      <span class="brand-name">Velran</span>
      <span class="brand-dot"></span>
    </div>
    <div class="contact-panel">
      <p class="person-name">Alden Marsh</p>
      <p class="person-role">Director</p>
      <p class="address">17 Marlow Yard, Upper Heath,<br>Warwick, CV31 8QL, United Kingdom</p>
      <ul class="contact-list">
        <li><svg viewBox="0 0 10 10" aria-hidden="true"><path d="M2 0.5l1.6 2.2-1 1c.6 1.3 1.5 2.2 2.7 2.7l1-1L9.5 7 8.3 9.3C4.4 9 1 5.6.7 1.7z"/></svg>1234567890</li>
        <li><svg viewBox="0 0 10 10" aria-hidden="true"><path d="M2.5 0h5a.8.8 0 0 1 .8.8v8.4a.8.8 0 0 1-.8.8h-5a.8.8 0 0 1-.8-.8V.8A.8.8 0 0 1 2.5 0zm.6 1.2v6.4h3.8V1.2z"/></svg>1234567890</li>
        <li><svg viewBox="0 0 10 10" aria-hidden="true"><path d="M0 2h10v6H0zm1 .6L5 5.4 9 2.6z" fill-rule="evenodd"/></svg>info@velran-example.co.uk</li>
        <li class="web"><svg viewBox="0 0 10 10" aria-hidden="true"><circle cx="5" cy="5" r="5"/></svg>www.velrancomponents-example.co.uk</li>
      </ul>
    </div>
  </section>

  <section class="card card-back" aria-label="Business card, brand side">
    <div class="brand-lockup">
      <span class="brand-dot"></span>
      <span class="brand-name">Velran Global Components</span>
    </div>
  </section>
</main>
</body>
</html>
```